Velmora Freightway Solutions Business cards

Would like a very unique design catchy but professional for business cards. Please use log provided.Marlon WellsCeo and Founder TransCon Logistix Solutions1-888-913-3225mwells@tlsolutionsus.comwww.tlsolutionsus.com

```html
<!DOCTYPE html>
<html lang="en">
<head>
<meta charset="utf-8">
<title>Velmora Freightway Solutions – Business Cards</title>
<link href="https://fonts.googleapis.com/css2?family=Lato:wght@400;700;900&display=swap" rel="stylesheet">
<style>
  :root {
    --backdrop: #1b1b1d;
    --card: #ffffff;
    --brand-blue: #1474c4;
    --deep-navy: #0f2a4a;
    --accent-red: #e2272f;
    --ink: #1d1d1f;
    --white: #ffffff;
  }
  * { margin: 0; padding: 0; box-sizing: border-box; }
  html, body {
    width: 1200px; height: 960px; overflow: hidden;
    background: var(--backdrop);
    font-family: "Lato", Arial, sans-serif;
  }
  .stage { position: relative; width: 1200px; height: 960px; }

  .card {
    position: absolute;
    width: 560px; height: 320px;
    background: var(--card);
    overflow: hidden;
    box-shadow: 0 18px 40px rgba(0,0,0,.55);
  }

  /* Logo-side card */
  .card--brand { left: 540px; top: 110px; }
  .brand-block {
    position: absolute; left: 0; right: 0; top: 92px;
    display: flex; flex-direction: column; align-items: center;
  }
  .brand-lockup { display: flex; align-items: center; gap: 14px; }
  .brand-square { width: 26px; height: 26px; background: var(--brand-blue); flex: none; }
  .brand-name {
    font-weight: 900; font-size: 30px; letter-spacing: 1px;
    color: var(--brand-blue); text-transform: uppercase; line-height: 1.1;
    text-align: center;
  }
  .brand-web {
    margin-top: 34px;
    display: flex; align-items: center; gap: 16px;
    font-size: 15px; letter-spacing: 3px; color: var(--ink); font-weight: 700;
  }
  .brand-web .rule { width: 70px; height: 2px; background: var(--brand-blue); }

  /* Contact card */
  .card--contact { left: 110px; top: 510px; }
  .contact-brand {
    position: absolute; left: 30px; top: 30px;
    display: flex; align-items: center; gap: 10px;
  }
  .contact-brand .brand-square { width: 18px; height: 18px; }
  .contact-brand .brand-name { font-size: 20px; text-align: left; }
  .contact-list {
    position: absolute; left: 30px; top: 76px; list-style: none;
    font-size: 14px; color: var(--ink); z-index: 2;
  }
  .contact-list li { display: flex; align-items: center; gap: 9px; height: 22px; }
  .contact-list svg { width: 12px; height: 12px; fill: var(--brand-blue); }
  .swoosh { position: absolute; left: 0; top: 0; width: 560px; height: 320px; z-index: 1; }
  .holder {
    position: absolute; right: 40px; bottom: 26px; text-align: right; color: var(--white);
    z-index: 2;
  }
  .holder-name { font-weight: 900; font-size: 22px; letter-spacing: .5px; line-height: 1.2; }
  .holder-role { font-size: 15px; letter-spacing: .5px; margin-top: 2px; }
</style>
</head>
<body>
<main class="stage">

  <section class="card card--brand">
    <div class="brand-block">
      <div class="brand-lockup">
        <span class="brand-square"></span>
        <span class="brand-name">Velmora Freightway<br>Solutions</span>
      </div>
      <div class="brand-web">
        <span class="rule"></span>
        <span>www.vfwayroutes.com</span>
        <span class="rule"></span>
      </div>
    </div>
  </section>

  <section class="card card--contact">
    <div class="contact-brand">
      <span class="brand-square"></span>
      <span class="brand-name">Velmora Freightway Solutions</span>
    </div>

    <ul class="contact-list">
      <li>
        <svg viewBox="0 0 24 24"><path d="M6.6 10.8a15.1 15.1 0 0 0 6.6 6.6l2.2-2.2a1 1 0 0 1 1-.25 11.4 11.4 0 0 0 3.6.57 1 1 0 0 1 1 1V20a1 1 0 0 1-1 1A17 17 0 0 1 3 4a1 1 0 0 1 1-1h3.5a1 1 0 0 1 1 1c0 1.25.2 2.45.57 3.57a1 1 0 0 1-.25 1z"/></svg>
        1-888-470-6158
      </li>
      <li>
        <svg viewBox="0 0 24 24"><path d="M2 5h20v14H2zm2 2v.4l8 5 8-5V7zm0 2.8V17h16V9.8l-8 5z"/></svg>
        dpike@vfwayroutes.com
      </li>
      <li>
        <svg viewBox="0 0 24 24"><path d="M12 2a10 10 0 1 0 0 20 10 10 0 0 0 0-20zm6.9 6h-3a15.6 15.6 0 0 0-1.4-3.6A8 8 0 0 1 18.9 8zM12 4c.8 1.2 1.5 2.5 1.9 4h-3.8c.4-1.5 1.1-2.8 1.9-4zM4.3 14a8 8 0 0 1 0-4h3.4a16 16 0 0 0 0 4zm.8 2h3a15.6 15.6 0 0 0 1.4 3.6A8 8 0 0 1 5.1 16zm3-8h-3a8 8 0 0 1 4.4-3.6A15.6 15.6 0 0 0 8.1 8zM12 20c-.8-1.2-1.5-2.5-1.9-4h3.8c-.4 1.5-1.1 2.8-1.9 4zm2.3-6H9.7a14 14 0 0 1 0-4h4.6a14 14 0 0 1 0 4zm.2 5.6a15.6 15.6 0 0 0 1.4-3.6h3a8 8 0 0 1-4.4 3.6zm1.8-5.6a16 16 0 0 0 0-4h3.4a8 8 0 0 1 0 4z"/></svg>
        www.vfwayroutes.com
      </li>
    </ul>

    <svg class="swoosh" viewBox="0 0 560 320" aria-hidden="true">
      <path d="M0 150 C 90 205, 210 222, 330 228" fill="none" stroke="var(--accent-red)" stroke-width="3"/>
      <path d="M0 178 C 140 236, 330 238, 560 192" fill="none" stroke="var(--deep-navy)" stroke-width="7"/>
      <path d="M0 200 C 140 252, 330 250, 560 206 L560 320 L0 320 Z" fill="var(--brand-blue)"/>
    </svg>

    <div class="holder">
      <div class="holder-name">DORIAN PIKE</div>
      <div class="holder-role">CEO AND FOUNDER</div>
    </div>
  </section>

</main>
</body>
</html>
```